Wordpress Theme for Northvale Clinics

** Please view updated Sitemap2.pdf doc to clarify some confusion ***

This is a multiuser WordPress subscription site for Northvale Clinics. Please see attachment for sitemap. Please do not include extra content like social media icons, search bars, or images. If you have questions, please ask for clarification.
The site contains the following pages and sub-pages:

1. Home
2. Our Clinic
2a. Our Clinic > Mission
2b. Our Clinic > Services
2c. Our Clinic > Clinic Policies
2d. Our Clinic > Schedules
3. Our Staff
3a. Our Staff > [Staff member page]
4. Resources
4a. Resources > Patient Health (index)
4b. Resources > Patient Health (index) > [post]
4c. Resources > Links
4d. Resources > Forms
5. Alerts
5a. Alerts > [Alert Page]
6. Contact Us

Includes the Following Pages, Subpages, and Content
1. Home
a. About Us
b. Our Staff
c. Bulletins
d. Accepting New Patients (shown as an alert widget)
e. Links
i. Physician Toolbox
ii. Book an Appointment
f. Clinic Policies
i. Show first 3 policies (e.g. Late Arrivals, Missed Appointments, Fees)
ii. Link to Clinic Policies page
g. Primary widget (displayed on all pages)
i. Hours of operation
ii. Contact Info
1. Tel
2. Fax
3. Email
4. Address
5. Get directions (link to Google Maps)
2. Our Clinic
a. Main Page
i. Clinic Name
ii. Overview
iii. Languages Spoken
iv. Secondary Navigation
1. Mission
2. Services
3. Clinic Policies
4. Schedules (see attachment)
b. Our Clinic > Mission
c. Our Clinic > Services
i. For each service include service TITLE and DESCRIPTION
d. Our Clinic > Clinic Policies
i. For each policy include policy TITLE and DESCRIPTION
ii. Include the following policies in mockup
1. Late arrivals
2. Missed appointments
3. Fees for missed appointments
4. Referrals and follow-ups
5. Services not covered by RDA
6. Information for LTF patients
7. Medical Legal Reports
e. Our Clinic > Schedules
3. Our Staff
a. Main Page
i. Display a list of staff members. Include NAME and DESIGNATION
b. Our Staff > [Staff Name]
i. Include NAME, PICTURE, DESIGNATION, and BIO
4. Resources
a. Resources > Patient Health
i. Main Page
1. Posts (ordered by date)
a. Title
b. Summary
2. Side Navigation
a. Post Categories
ii. Patient Health > [post title]
1. Title
2. Post Category
3. Date
4. Author
5. Summary
6. Body
b. Resources > Links
1. Secondary Navigation - Categories
a. Sample Categories:
i. Local Services
ii. RDA and Drug Coverage
iii. Mental Health Resources
2. Category page
a. Include the following links in the 'Local Services' category
i. Hypertension clinics
ii. Home Care services
iii. Vaccine Clinics
c. Resources > Forms
i. Display a table with form TITLE and CATEGORY
ii. Side Navigation
1. Form Categories
a. Use the following sample Categories
i. Referrals
ii. Insurance
iii. Intake
iv. Discharge
v. Waivers
5. Alerts
a. Main page
i. List of all Alert posts
1. Include post TITLE as a link to the post
ii. Side Navigation
1. Alerts Archive
a. shown as Month + Number of posts
iii. Alerts > [Alert page]
1. Include TITLE, DATE, AUTHOR, BODY
6. Contact Us
a. Map
b. Hours of operation
c. Address
d. Phone number
e. Fax number
e. Fax number
f. Map
g. Email

Design notes:
- fixed width
- responsive (need designs for mobile, tablet, and desktop)
- simple, dark font, white background
- use Font Awesome icons where needed
- user adds own logo

Target Market(s)

Northvale Clinics

Industry/Entity Type

Medical

Number of Pages Required

5+ page

Font styles to use
Serif
Sans Serif

Requirements
Must have
• Please keep designs very simple.
• Examples:
• https://www.quolbin.com/install
• http://www.ventrohax.com/company/about-us
• http://brindlequota.org/
• http://www.trosk.com/
Should not have
• Minimal or no use of shadows and gradients

```html
<!DOCTYPE html>
<html lang="en">
<head>
<meta charset="utf-8">
<title>Alerts – Northvale Clinics</title>
<link href="https://fonts.googleapis.com/css2?family=Open+Sans:wght@400;600;700&display=swap" rel="stylesheet">
<style>
:root{
  --blue:#0a87dc;
  --blue-dark:#0a7ccc;
  --ink:#222;
  --text:#333;
  --muted:#777;
  --band:#f7f7f7;
  --rule:#d6d6d6;
  --footer:#262626;
  --footer-text:#8a8a8a;
  --footer-head:#a9a9a9;
  --white:#fff;
}
*{margin:0;padding:0;box-sizing:border-box}
html,body{width:1200px;height:975px;overflow:hidden;background:var(--white)}
body{font-family:"Open Sans",Arial,sans-serif;color:var(--text);position:relative}
a{color:inherit;text-decoration:none}
.abs{position:absolute}

.topbar{left:0;top:0;width:1200px;height:30px;background:var(--blue);color:var(--white);font-size:10px}
.topbar .contact{left:161px;top:8px}
.topbar .contact span{border-right:1px solid var(--white);padding-right:4px;margin-right:4px}
.topbar .quick{right:161px;top:8px}
.topbar .quick a+a{border-left:1px solid var(--white);padding-left:6px;margin-left:6px}

.header{left:0;top:30px;width:1200px;height:82px}
.brand{left:161px;top:27px;display:flex;align-items:center;gap:12px;font-size:21px;font-weight:600;color:var(--ink)}
.brand-dot{width:22px;height:22px;border-radius:50%;background:var(--blue)}
.main-nav{top:0;left:0}
.main-nav a{position:absolute;top:34px;font-size:11px;color:var(--ink);white-space:nowrap}
.main-nav a.is-active{top:0;left:895px;width:60px;height:82px;background:var(--blue);color:#1a4f80;text-align:center;padding-top:34px}

.page-title{left:0;top:112px;width:1200px;height:60px;background:var(--band)}
.page-title h1{position:absolute;left:161px;top:16px;font-size:11px;font-weight:700;color:var(--ink)}
.page-title .crumbs{position:absolute;left:162px;top:35px;font-size:10px;color:var(--ink)}

.section-head{left:161px;top:208px;font-size:12px;font-weight:600;color:var(--ink)}
.section-rule{left:161px;top:234px;width:127px;height:2px;background:var(--rule)}

.alert{left:161px;width:655px}
.date-badge{position:absolute;left:0;top:3px;width:52px;height:44px;background:var(--blue-dark);color:var(--white);text-align:center;font-weight:700;line-height:1}
.date-badge .month{display:block;font-size:15px;padding-top:6px}
.date-badge .day{display:block;font-size:13px;padding-top:4px}
.date-badge sup{font-size:8px}
.alert h2{position:absolute;left:75px;top:0;width:580px;font-size:13px;font-weight:700;line-height:18px;color:var(--ink)}
.alert h2.is-current{color:var(--blue-dark)}
.alert p{position:absolute;left:75px;top:41px;width:580px;font-size:9.5px;line-height:15px;color:var(--ink)}

.load-more{left:446px;top:694px;width:98px;height:27px;background:var(--blue);color:var(--white);font-size:12px;text-align:center;line-height:27px;border-radius:2px}

.archives{left:835px;top:209px;width:204px;height:247px;border:1px solid var(--rule)}
.archives-head{height:32px;background:var(--blue);color:var(--white);font-size:10px;font-weight:700;display:flex;align-items:center;gap:9px;padding-left:14px}
.archives ul{list-style:none;padding:15px 0 0 17px}
.archives li{display:flex;font-size:10.5px;line-height:18px;color:var(--ink)}
.archives li .month{width:105px}
.archives li.is-current{color:var(--blue)}

.footer-stripe{left:0;top:747px;width:1200px;height:5px;background:var(--blue)}
.footer{left:0;top:752px;width:1200px;height:223px;background:var(--footer);color:var(--footer-text);font-size:10px}
.footer .brand{top:40px;color:var(--white)}
.footer .about{left:162px;top:85px;width:205px;font-size:9px;line-height:14px;color:#cfcfcf}
.footer h3{position:absolute;font-size:12px;font-weight:600;color:var(--footer-head)}
.footer ul{position:absolute;list-style:none}
.footer li{line-height:18px}
.footer li.is-current{color:#ddd}
.footer dl{position:absolute;left:838px;top:56px;display:grid;grid-template-columns:90px auto;line-height:15px}
.footer dd{color:var(--footer-text)}
.footer-bottom{left:0;top:188px;width:1200px;border-top:1px solid #444;height:35px}
.footer-bottom span{position:absolute;top:10px}
</style>
</head>
<body>

<div class="abs topbar">
  <div class="abs contact"><span>To help Here : 222 333 4444</span>Email : hello@northvale.example</div>
  <div class="abs quick"><a href="#">Book an Appointment</a><a href="#">Physician Toolbox</a></div>
</div>

<header class="abs header">
  <a class="abs brand" href="#"><span class="brand-dot"></span>Northvale Clinics</a>
  <nav class="abs main-nav">
    <a href="#" style="left:586px">Home</a>
    <a href="#" style="left:654px">Our Clinic</a>
    <a href="#" style="left:741px">Our Staff</a>
    <a href="#" style="left:824px">Resources</a>
    <a href="#" class="is-active">Alerts</a>
    <a href="#" style="left:977px">Contact Us</a>
  </nav>
</header>

<div class="abs page-title">
  <h1>ALERTS</h1>
  <div class="crumbs">HOME / ALERTS</div>
</div>

<h2 class="abs section-head">ALERTS/BULLETINS</h2>
<div class="abs section-rule"></div>

<article class="abs alert" style="top:256px">
  <div class="date-badge"><span class="month">June</span><span class="day">25<sup>th</sup></span></div>
  <h2 class="is-current">Lorem Ipsum is simply dummy text of the printing and typesetting industry. Lorem Ipsum has been the industry's</h2>
  <p>Contrary to popular belief, Lorem Ipsum is not simply random text. It has roots in a piece of classical Latin literature from 45 BC, making it over 2000 years old. Harold Benwick, a Latin professor at Ashford-Lyle College in Vermont, looked up one of the more obscure Latin words,</p>
</article>
<article class="abs alert" style="top:363px">
  <div class="date-badge"><span class="month">June</span><span class="day">24<sup>th</sup></span></div>
  <h2>Lorem Ipsum is simply dummy text of the printing and typesetting industry. Lorem Ipsum has been the industry's</h2>
  <p>Contrary to popular belief, Lorem Ipsum is not simply random text. It has roots in a piece of classical Latin literature from 45 BC, making it over 2000 years old. Harold Benwick, a Latin professor at Ashford-Lyle College in Vermont, looked up one of the more obscure Latin words,</p>
</article>
<article class="abs alert" style="top:470px">
  <div class="date-badge"><span class="month">June</span><span class="day">23<sup>th</sup></span></div>
  <h2>Lorem Ipsum is simply dummy text of the printing and typesetting industry. Lorem Ipsum has been the industry's</h2>
  <p>Contrary to popular belief, Lorem Ipsum is not simply random text. It has roots in a piece of classical Latin literature from 45 BC, making it over 2000 years old. Harold Benwick, a Latin professor at Ashford-Lyle College in Vermont, looked up one of the more obscure Latin words,</p>
</article>
<article class="abs alert" style="top:577px">
  <div class="date-badge"><span class="month">June</span><span class="day">22<sup>th</sup></span></div>
  <h2>Lorem Ipsum is simply dummy text of the printing and typesetting industry. Lorem Ipsum has been the industry's</h2>
  <p>Contrary to popular belief, Lorem Ipsum is not simply random text. It has roots in a piece of classical Latin literature from 45 BC, making it over 2000 years old. Harold Benwick, a Latin professor at Ashford-Lyle College in Vermont, looked up one of the more obscure Latin words,</p>
</article>

<a class="abs load-more" href="#">Loard more</a>

<aside class="abs archives">
  <div class="archives-head">
    <svg width="13" height="13" viewBox="0 0 13 13" aria-hidden="true"><rect x="0.5" y="1.5" width="12" height="11" fill="none" stroke="#fff"/><rect x="0.5" y="1.5" width="12" height="3" fill="#fff"/><g fill="#fff"><rect x="2.5" y="6" width="2" height="2"/><rect x="5.5" y="6" width="2" height="2"/><rect x="8.5" y="6" width="2" height="2"/><rect x="2.5" y="9" width="2" height="2"/><rect x="5.5" y="9" width="2" height="2"/><rect x="8.5" y="9" width="2" height="2"/></g></svg>
    ALERTS ARCHIVES
  </div>
  <ul>
    <li class="is-current"><span class="month">June 2015</span><span>200 posts</span></li>
    <li><span class="month">May 2015</span><span>250 posts</span></li>
    <li><span class="month">April 2015</span><span>480 posts</span></li>
    <li><span class="month">March 2015</span><span>180 posts</span></li>
    <li><span class="month">February 2015</span><span>380 posts</span></li>
    <li><span class="month">January 2015</span><span>580 posts</span></li>
  </ul>
</aside>

<div class="abs footer-stripe"></div>
<footer class="abs footer">
  <a class="abs brand" href="#"><span class="brand-dot"></span>Northvale Clinics</a>
  <p class="abs about">Lorem Ipsum is simply dummy text of the printing and typesetting industry. Lorem Ipsum has been the industry's standard dummy text</p>

  <h3 style="left:461px;top:31px">Navigation</h3>
  <ul style="left:461px;top:54px">
    <li class="is-current">Home</li><li>Our Clinic</li><li>Newsletter</li><li>Our Staff</li><li>Resources</li>
  </ul>

  <h3 style="left:686px;top:31px">Links</h3>
  <ul style="left:686px;top:54px">
    <li>Help</li><li>Support</li><li>Privacy Policy</li>
  </ul>

  <h3 style="left:836px;top:30px">Contact Us</h3>
  <dl>
    <dt>Telephone :</dt><dd>250-555-0147</dd>
    <dt>Email:</dt><dd>hello@northvale.example</dd>
    <dt>Address:</dt><dd>48 Cedar Lane<br>Harrowby, B. Canada,<br>K2P 4RT</dd>
  </dl>

  <div class="abs footer-bottom">
    <span style="left:162px">© 2015 Northvale Clinics. All Rights Reservsd</span>
    <span style="left:463px">About Us</span>
    <span style="left:530px">Terms of Use</span>
    <span style="left:615px">Privacy Policy</span>
    <span style="right:164px">Site design &amp; developed by Pinecrest Web Studio</span>
  </div>
</footer>

</body>
</html>
```